Debt Collection Website Design! We are the solution for landlords to get paid what they are owed.

We are a 3rd party debt collection company that specializes in Residential and Commercial real estate debt collection. We help landlords recover money from past residents by being fair, friendly and aggressive. We also collect/buy/sell/trade civil judgments won resulting from anything from automobile accidents to evictions to a pet zebra getting stolen. We buy single judgments to large portfolios, we also collect judgments for a nominal fee.

I would like a new, modern, easy to navigate website. A spot that we can post news stories or updated information about our company. I have included our company logo that must be on the top of the page. Feel free to ask any questions that will help get the process going.

Target Market(s)

Landlords, small to large apartment complex. Real estate services and lawyers.

Industry/Entity Type

Real Estate

Number of Pages Required

3 page

Requirements
Must have
• Company logo which has been attached. A page where we can explain the collection process, fees and placement. A page where we can explain judgments, collection vs. selling, placement form. I am open to any font/designs and willing to work with anyone.
Nice to have
• Nice to have a spot on the homepage to place news articles about ourselves and our industry.
Should not have
• I don't want it over crowded. Simple, sleek and easy to navigate is best. No gavels on any of the pages. It cannot look legal, say/show anything that we use legal powers to collect. We are not a law office, we don't practice law, we are 3rd party debt collection agency.

```html
<!DOCTYPE html>
<html lang="en">
<head>
<meta charset="utf-8">
<title>Marlowe Recovery, LLC</title>
<link href="https://fonts.googleapis.com/css2?family=Open+Sans:ital,wght@0,400;0,600;0,700;1,700&display=swap" rel="stylesheet">
<style>
:root{
  --blue:#4a70b8;
  --navy:#1f3a78;
  --band:#e9eaf3;
  --text:#666;
  --heading:#333;
  --grey-head:#8a8a8a;
  --rule:#e2e2e2;
  --footer:#1e1e1e;
  --date:#c0392b;
}
*{margin:0;padding:0;box-sizing:border-box}
html,body{width:747px;height:1200px;overflow:hidden}
body{position:relative;background:#fff;font-family:"Open Sans",sans-serif;color:var(--text)}
.abs{position:absolute}
/* header */
.header{left:0;top:0;width:747px;height:78px;border-bottom:1px solid #ddd;background:#fff}
.brand{left:62px;top:24px;display:flex;align-items:center;gap:8px}
.brand-mark{width:26px;height:26px;background:var(--navy)}
.brand-name{font-size:17px;font-weight:600;color:var(--navy);line-height:1.05}
.brand-name small{display:block;font-size:10px;letter-spacing:.5px}
.nav{left:328px;top:34px;display:flex;font-size:7.5px;color:#333;text-transform:uppercase}
.nav span{margin-right:9px}
.nav .sep{color:#555}
.nav .active{color:var(--blue)}
.search{left:666px;top:29px;width:20px;height:20px;border-radius:50%;background:#eef0f5}
/* hero */
.hero-band{left:0;top:78px;width:747px;height:376px;background:var(--band)}
.hero-photo{left:62px;top:78px;width:624px;height:287px;background:linear-gradient(110deg,#e9e4dc 0%,#c9c2b6 30%,#5a6478 55%,#2c3550 80%,#3a4a78 100%)}
.hero-caption{left:112px;top:192px;width:328px;height:56px;background:rgba(70,70,70,.85);color:#fff;font-weight:700;font-size:12.5px;line-height:18px;padding:10px 13px}
.hero-arrow{top:210px;width:23px;height:22px;background:rgba(40,40,40,.7)}
.welcome{left:0;top:373px;width:747px;text-align:center}
.welcome h2{color:var(--blue);font-size:12px;font-weight:700}
.welcome p{font-size:6.6px;line-height:12.5px;width:540px;margin:7px auto 0}
.welcome a{display:block;margin-top:5px;font-size:6.5px;font-weight:700;font-style:italic;color:var(--blue)}
/* specialties */
.spec-title{left:62px;top:474px;font-size:12.5px;color:var(--heading)}
.spec-rule{left:62px;top:503px;width:624px;height:1px;background:var(--rule)}
.spec-photo{top:524px;width:137px;height:106px;border:2px solid #fff;box-shadow:0 0 2px #bbb}
.spec-card h3{font-size:8.5px;font-weight:600;color:var(--heading);margin-bottom:10px}
.spec-card p{font-size:6.6px;line-height:12.3px;text-align:justify;width:146px}
/* services */
.services-title{left:0;top:670px;width:747px;text-align:center;font-size:20px;font-weight:700;color:var(--grey-head)}
.service{top:733px;width:140px;text-align:center}
.service .icon{width:38px;height:39px;border:1px solid #333;margin:0 auto;display:flex;align-items:center;justify-content:center}
.service .icon.hl{border-color:var(--blue)}
.service h4{font-size:8.5px;font-weight:600;color:#333;margin-top:10px}
.service h4.hl{color:var(--blue)}
.service p{font-size:6.6px;line-height:12px;margin-top:6px}
/* news */
.news-band{left:0;top:885px;width:747px;height:43px;background:var(--blue);color:#fff;text-align:center;font-size:14px;line-height:43px}
.news-pointer{left:363px;top:927px}
.news-photo{left:341px;top:951px;width:64px;height:64px;border-radius:50%;border:3px solid #eee;background:linear-gradient(135deg,#dfe6ee,#7d8ea8 60%,#3b4a66)}
.news-body{left:0;top:1022px;width:747px;text-align:center}
.news-body h3{font-size:11px;font-weight:600;color:#333}
.news-body p{font-size:6.6px;line-height:12.5px;width:520px;margin:6px auto 0}
.news-meta{margin-top:6px;font-size:7px}
.news-meta .date{color:var(--date)}
.news-meta .comment{color:#888;margin-left:8px}
.pager{left:365px;top:1104px;display:flex;gap:2px}
.pager span{width:16px;height:12px;background:#888}
.news-rule{left:294px;top:1130px;width:159px;height:1px;background:var(--rule)}
/* footer */
.footer{left:0;top:1148px;width:747px;height:52px;background:var(--footer)}
.footer-links{left:62px;top:1161px;font-size:6.8px;color:#777}
.footer-copy{left:62px;top:1178px;font-size:6.3px;color:#666}
.social{top:1162px;width:23px;height:23px;border-radius:50%;border:1px solid #777}
</style>
</head>
<body>
<header class="abs header">
  <div class="abs brand">
    <div class="brand-mark"></div>
    <div class="brand-name">MARLOWE<small>RECOVERY, LLC</small></div>
  </div>
  <nav class="abs nav">
    <span class="active">Home</span><span class="sep">/</span>
    <span>Services</span><span class="sep">/</span>
    <span>About Us</span><span class="sep">/</span>
    <span>News</span><span class="sep">/</span>
    <span>Features</span><span class="sep">/</span>
    <span>Conatct</span>
  </nav>
  <div class="abs search">
    <svg width="20" height="20" viewBox="0 0 20 20"><circle cx="9" cy="9" r="3" fill="none" stroke="#3a5a9a" stroke-width="1.4"/><line x1="11.2" y1="11.2" x2="13.5" y2="13.5" stroke="#3a5a9a" stroke-width="1.6"/></svg>
  </div>
</header>

<section>
  <div class="abs hero-band"></div>
  <div class="abs hero-photo" role="img" aria-label="Two smiling businessmen in suits reviewing documents at a desk"></div>
  <div class="abs hero-caption">SPECIALIZES IN RESIDENTIAL AND COMMERCIAL REAL&nbsp; ESTATE DEBT COLLECTION</div>
  <div class="abs hero-arrow" style="left:62px"><svg width="23" height="22"><polyline points="14,5 9,11 14,17" fill="none" stroke="#fff" stroke-width="1"/></svg></div>
  <div class="abs hero-arrow" style="left:663px"><svg width="23" height="22"><polyline points="9,5 14,11 9,17" fill="none" stroke="#fff" stroke-width="1"/></svg></div>
  <div class="abs welcome">
    <h2>WELCOME</h2>
    <p>"Sed ut perspiciatis unde omnis iste natus error sit voluptatem accusantium doloremque laudantium, totam rem aperiam, eaque ipsa quae ab illo inventore veritatis et quasi architecto beatae vitae dicta sunt explicabo. Nemo enim ipsam voluptatem quia voluptas sit aspernatur"</p>
    <a>Read More +</a>
  </div>
</section>

<section>
  <h2 class="abs spec-title">WE ARE SPECIALIZES</h2>
  <div class="abs spec-rule"></div>
  <div class="abs spec-photo" style="left:62px;background:linear-gradient(180deg,#3f6fb8 0%,#8fb0d8 30%,#efe9dc 55%,#d8cfbf 75%,#2a8fc7 100%)" role="img" aria-label="White villa with swimming pool"></div>
  <div class="abs spec-card" style="left:216px;top:524px">
    <h3>Residential Debt</h3>
    <p>But I must explain to you how all this mistaken idea of denouncing pleasure and praising pain was born and I will give you a complete account of the system, and expound the actual teachings of the great quences that are extremely painful.</p>
  </div>
  <div class="abs spec-photo" style="left:387px;background:linear-gradient(90deg,#1d3f8f 0%,#3f78c8 35%,#9cc4e8 50%,#4a7fc2 70%,#16306e 100%)" role="img" aria-label="Blue glass office towers"></div>
  <div class="abs spec-card" style="left:541px;top:524px">
    <h3>Commercial Debt</h3>
    <p>But I must explain to you how all this mistaken idea of denouncing pleasure and praising pain was born and I will give you a complete account of the system, and expound the actual teachings of the great quences that are extremely painful.</p>
  </div>
</section>

<section>
  <h2 class="abs services-title">SERVICES</h2>
  <div class="abs service" style="left:58px">
    <div class="icon hl"><svg width="18" height="12" viewBox="0 0 18 12"><rect x="1" y="1" width="16" height="10" fill="none" stroke="var(--blue)" stroke-width="2"/><circle cx="9" cy="6" r="2.6" fill="var(--blue)"/></svg></div>
    <h4 class="hl">COLLECTION</h4>
    <p>Lorem ipsum dolor sit amet, consectetur adipiscing elit, sed do eiusmod tempor ut labore et dolore magna aliqua. Ut</p>
  </div>
  <div class="abs service" style="left:220px">
    <div class="icon"><svg width="16" height="16" viewBox="0 0 16 16" fill="none" stroke="#333" stroke-width="1.6"><circle cx="8" cy="3" r="1.5"/><line x1="8" y1="4.5" x2="8" y2="14"/><line x1="5" y1="7" x2="11" y2="7"/><path d="M2 10 Q4 14 8 14 Q12 14 14 10"/></svg></div>
    <h4>BUY</h4>
    <p>Lorem ipsum dolor sit amet, consectetur adipiscing elit, sed do eiusmod tempor ut labore et dolore magna aliqua. Ut</p>
  </div>
  <div class="abs service" style="left:385px">
    <div class="icon"><svg width="16" height="16" viewBox="0 0 16 16" fill="#333"><rect x="1" y="7" width="3" height="7"/><path d="M5 7 L8 2 Q10 2 9.5 5 L14 5 Q15 6 14.5 8 L13 13.5 Q12.5 14 12 14 L5 14 Z"/></svg></div>
    <h4>SELL</h4>
    <p>Lorem ipsum dolor sit amet, consectetur adipiscing elit, sed do eiusmod tempor ut labore et dolore magna aliqua. Ut</p>
  </div>
  <div class="abs service" style="left:549px">
    <div class="icon"><svg width="16" height="16" viewBox="0 0 16 16"><circle cx="8" cy="8" r="5" fill="none" stroke="#333" stroke-width="3" stroke-dasharray="2.5 1.4"/><circle cx="8" cy="8" r="4" fill="none" stroke="#333" stroke-width="2.4"/></svg></div>
    <h4>TRADE</h4>
    <p>Lorem ipsum dolor sit amet, consectetur adipiscing elit, sed do eiusmod tempor ut labore et dolore magna aliqua. Ut</p>
  </div>
</section>

<section>
  <h2 class="abs news-band" style="font-weight:400">LATEST NEWS</h2>
  <svg class="abs news-pointer" width="20" height="11"><polygon points="0,0 20,0 10,10" fill="var(--blue)"/></svg>
  <div class="abs news-photo" role="img" aria-label="Business presentation in a meeting room"></div>
  <div class="abs news-body">
    <h3>passages of Lorem Ipsum available</h3>
    <p>must explain to you how all this mistaken idea of denouncing pleasure and praising pain was born and I will give you a complete account of the system, and expound the actual teachings of the great explorer of the truth, the master-builder of human happiness. No one rejects</p>
    <div class="news-meta">
      <span class="date">
        <svg width="7" height="7" viewBox="0 0 7 7"><rect x=".5" y="1" width="6" height="5.5" fill="none" stroke="var(--date)"/><line x1=".5" y1="2.6" x2="6.5" y2="2.6" stroke="var(--date)"/></svg>
        27 FEB 2015</span>
      <span class="comment">
        <svg width="8" height="7" viewBox="0 0 8 7"><ellipse cx="4" cy="3" rx="3.6" ry="2.5" fill="#888"/><polygon points="2,4.5 1,7 4,5" fill="#888"/></svg>
        Comment 0</span>
    </div>
  </div>
  <div class="abs pager">
    <span><svg width="16" height="12"><circle cx="8" cy="6" r="3.5" fill="#fff"/><polyline points="8.8,4.3 7,6 8.8,7.7" fill="none" stroke="#888"/></svg></span>
    <span><svg width="16" height="12"><circle cx="8" cy="6" r="3.5" fill="#fff"/><polyline points="7.2,4.3 9,6 7.2,7.7" fill="none" stroke="#888"/></svg></span>
  </div>
  <div class="abs news-rule"></div>
</section>

<footer class="abs footer"></footer>
<div class="abs footer-links">Home | Services | Aboutus | News | Features | Contact</div>
<div class="abs footer-copy">Copyright &copy; 2015 &nbsp;marlowe recovery. &nbsp; Allrights Reserved</div>
<div class="abs social" style="left:609px"></div>
<div class="abs social" style="left:635px"></div>
<div class="abs social" style="left:662px"></div>
</body>
</html>
```